The World Most Wanted Eyelahes

1. We need a web design for a new company based in California, USA
2. We are the manufacturer for 100% human hair eyelashes,
made in Indonesia.
3. We recently launched "Tapered Eyelashes" with human hair.
Currently, none of the people carried Tapered eyelash.
4. We would like to see designs that use the 4 different colors that match with my products as "Four Seasons" concepts.
5. We prefer to follow www.pelvo.com style, like professional website.
6. Focus on products as a manufacturer, therefore, all wholesaler and retailer copy and paste to their marketing tools.
7. Need bilingual English and Spanish.
8. Easy to link with social media.

Target Market(s)

United States and Central/South America.

Industry/Entity Type

Hair

Number of Pages Required

5+ page

Requirements
Must have
• 1. Details of Products with image.
• 2. Hottest/Newest Items "Tapered in 100% Human Hair"
• 3. Store Page
Nice to have
• 1. My competitors is Quorim Eyelash. http://www.quorimlashes.com/
• Please follow the concepts of it.
• 2. www.Pelvo.com: They have great products detail on the website.
• i would like to focus on "Tapered" for new styles of the eyelash.
• 3. I want to visitors can write down the "Reviews" in every single product.
• Please check the www.QTRCosmetics.com.
Should not have
• It's not salon/Shop for the beauty.
• No need an appointment.
• We are the manufacturer of the eyelash.

```html
<!DOCTYPE html>
<html lang="en">
<head>
<meta charset="utf-8">
<title>Velqa Eyelashes</title>
<link href="https://fonts.googleapis.com/css2?family=Open+Sans:ital,wght@0,400;0,600;0,700;1,400&family=Tinos:ital@0;1&display=swap" rel="stylesheet">
<style>
  :root{
    --ink:#222;
    --header:#231f20;
    --nav:#1a1a1a;
    --gold:#c0882e;
    --gold-soft:#c79a4a;
    --muted:#9a9a9a;
    --red:#c8242c;
    --blue:#5399bb; --blue-dark:#3d82a6;
    --rose:#d65e6c; --rose-dark:#c44b59;
    --violet:#943fa6; --violet-dark:#7c2f8f;
    --amber:#cda63c; --amber-dark:#bb932c;
    --line:#dcdcdc;
  }
  *{box-sizing:border-box;margin:0;padding:0}
  html,body{width:864px;height:1200px;overflow:hidden;background:#fff}
  body{position:relative;font-family:'Open Sans',Arial,sans-serif;color:var(--ink)}

  .site-header{position:absolute;left:0;top:0;width:864px;height:86px;background:var(--header)}
  .brand{position:absolute;left:71px;top:18px;color:var(--gold-soft);font-family:'Open Sans',Arial,sans-serif;font-weight:400}
  .brand .name{font-size:34px;letter-spacing:1px;line-height:36px}
  .brand .tag{font-size:9px;letter-spacing:4px;line-height:10px}
  .utility{position:absolute;top:20px;right:69px;display:flex;gap:38px;font-size:9px;color:#8d8d8d}
  .utility .cart{color:#b0894a}
  .utility .cart b{font-weight:400;color:#d4a13a}
  .lang{position:absolute;left:548px;top:48px;width:78px;height:23px;border:1px solid #444;font-size:8px;color:#999;padding:5px 7px;display:flex;align-items:center;gap:5px}
  .search{position:absolute;left:635px;top:48px;width:158px;height:23px;border:1px solid #444;font-size:8px;color:#888;padding:5px 9px}

  .main-nav{position:absolute;left:0;top:86px;width:864px;height:35px;background:var(--nav);display:flex;align-items:center;padding-left:83px;font-size:9.5px;color:#9c9c9c}
  .main-nav span{margin-right:27px}
  .main-nav .active{color:var(--gold)}

  .hero{position:absolute;left:71px;top:134px;width:722px;height:308px;overflow:hidden;
    background:linear-gradient(100deg,#f1ebe3 0%,#efe2da 45%,#e9c7c9 70%,#dcb0c6 100%)}
  .hero-photo{position:absolute;right:0;top:0;width:440px;height:308px;
    background:radial-gradient(ellipse at 70% 45%,#e8c0a8 0%,#e2bfb7 35%,rgba(226,190,200,0) 70%)}
  .hero h1{position:absolute;left:58px;top:38px;font-size:37px;line-height:42px;font-weight:700;color:var(--gold)}
  .hero h1 .dark{display:block;color:#1b1b1b}
  .hero .lede{position:absolute;left:63px;top:132px;font-family:'Tinos',serif;font-style:italic;font-size:18px;line-height:27px;color:#222}
  .hero .lede .hot{color:var(--gold);font-size:25px;font-weight:700}
  .btn-gold{position:absolute;left:63px;top:225px;width:158px;height:38px;background:var(--gold);color:#fff;font-size:11.5px;font-weight:700;letter-spacing:.5px;display:flex;align-items:center;justify-content:center;border-radius:2px}
  .slide-arrow{position:absolute;top:137px;width:30px;height:30px;background:rgba(255,255,255,.25)}

  .offer{position:absolute;left:71px;top:452px;width:722px;height:52px;border:1px solid var(--line);padding:2px}
  .offer div{width:100%;height:100%;border:1px solid #ccc;background:#f6f6f6;display:flex;align-items:center;justify-content:center;font-family:'Tinos',serif}
  .offer .big{font-size:20px;color:var(--red);margin-right:6px}
  .offer em{font-size:15px;color:#333}

  .products{position:absolute;left:71px;top:518px;width:724px;display:flex;gap:15px}
  .card{width:170px;height:284px;border:1px solid var(--line);border-bottom:0}
  .card .shot{height:172px;display:flex;align-items:center;justify-content:center}
  .card .shot div{width:112px;height:130px;border-radius:18px 18px 10px 10px}
  .card .info{height:82px;color:#fff;text-align:center;padding-top:13px}
  .card .info p{font-size:8.6px;font-weight:700;line-height:14.5px}
  .card .info .price{font-size:21px;font-weight:700;line-height:30px;margin-top:1px}
  .card .more{height:30px;color:#fff;font-size:11px;font-weight:700;letter-spacing:.4px;display:flex;align-items:center;justify-content:center}
  .blue .info{background:var(--blue)} .blue .more{background:var(--blue-dark)}
  .rose .info{background:var(--rose)} .rose .more{background:var(--rose-dark)}
  .violet .info{background:var(--violet)} .violet .more{background:var(--violet-dark)}
  .amber .info{background:var(--amber)} .amber .more{background:var(--amber-dark)}

  .about h2{position:absolute;left:73px;top:824px;font-size:14px;font-weight:700}
  .about p{position:absolute;left:71px;top:853px;width:722px;font-size:6.3px;line-height:14.8px;text-transform:uppercase;color:#555}

  .rule{position:absolute;left:71px;width:722px;height:1px;background:var(--line)}
  .newsletter{position:absolute;left:75px;top:942px;font-size:9.5px;color:#333}
  .email{position:absolute;left:319px;top:938px;width:186px;height:23px;border:1px solid #ddd;font-size:6.5px;color:#999;padding:7px 11px}
  .subscribe{position:absolute;left:513px;top:938px;width:105px;height:23px;background:var(--gold);color:#fff;font-size:7px;display:flex;align-items:center;justify-content:center}
  .social{position:absolute;left:681px;top:939px;display:flex;gap:5px}
  .social span{width:22px;height:22px;border-radius:50%}

  .footer-col{position:absolute;top:1000px}
  .footer-col h3{font-size:11px;font-weight:400;color:#333;margin-bottom:9px}
  .footer-col li{list-style:none;font-size:7px;letter-spacing:.5px;line-height:14.7px;color:#444;text-transform:uppercase}
  .footer-brand{position:absolute;left:654px;top:1022px;color:var(--gold-soft)}
  .footer-brand .name{font-size:34px;line-height:36px;letter-spacing:1px}
  .footer-brand .tag{font-size:9px;letter-spacing:4px;color:#555}
  .copyright{position:absolute;left:0;width:864px;top:1162px;text-align:center;font-size:6.8px;letter-spacing:.6px;color:#444}
</style>
</head>
<body>

<header class="site-header">
  <div class="brand"><div class="name">VELQA</div><div class="tag">EYELASHES</div></div>
  <div class="utility">
    <span>My Account</span><span>My Cart</span><span>Login</span><span>Register</span>
    <span class="cart"><svg width="9" height="8" viewBox="0 0 9 8" style="vertical-align:-1px;margin-right:4px"><path d="M0 1h1.6l1 4h4.6l1-3H2.3" fill="none" stroke="#d4a13a" stroke-width="1"/><circle cx="3.2" cy="6.8" r=".8" fill="#d4a13a"/><circle cx="6.6" cy="6.8" r=".8" fill="#d4a13a"/></svg>Your cart is : <b>0 Items</b></span>
  </div>
  <div class="lang"><svg width="11" height="7"><rect width="11" height="7" fill="#3a4a8a"/></svg>English<svg width="6" height="4" style="margin-left:auto"><path d="M0 0l3 3 3-3" fill="none" stroke="#999"/></svg></div>
  <div class="search">Search<svg width="9" height="9" style="position:absolute;right:8px;top:7px"><circle cx="3.8" cy="3.8" r="2.8" fill="none" stroke="#999" stroke-width="1.2"/><path d="M6 6l2.5 2.5" stroke="#999" stroke-width="1.2"/></svg></div>
</header>

<nav class="main-nav">
  <span class="active">HOME</span><span>/</span><span>PRODUCTS</span><span>/</span><span>SERVICES</span><span>/</span><span>ONLIN E SHOP</span><span>/</span><span>ABOUT US</span><span>/</span><span>CONTACT US</span>
</nav>

<section class="hero">
  <div class="hero-photo" role="img" aria-label="Model with long lashes beside two packs of tapered eyelashes"></div>
  <h1>TAPERED IN 100%<span class="dark">HUMAN HAIR</span></h1>
  <div class="lede">WE RECENTLY LAUNCHED<br><span class="hot">TAPERED EYELASHES</span><br>WITH HUMAN HAIR</div>
  <div class="btn-gold">VIEW ALL PRODUCTS</div>
  <div class="slide-arrow" style="left:0"><svg width="30" height="30"><path d="M18 9l-6 6 6 6" fill="none" stroke="#fff" stroke-width="1"/></svg></div>
  <div class="slide-arrow" style="right:0"><svg width="30" height="30"><path d="M12 9l6 6-6 6" fill="none" stroke="#fff" stroke-width="1"/></svg></div>
</section>

<div class="offer"><div><span class="big">FREE SHIPPING ON ORDERS OVER $ 80.</span><em>This offer is valid on all our Store items</em></div></div>

<section class="products">
  <article class="card blue">
    <div class="shot"><div role="img" aria-label="Eyelash pack, blue edition" style="background:linear-gradient(160deg,#e3e8ee,#c9d6e2)"></div></div>
    <div class="info"><p>LOREM IPSUM IS SIMPLY DUMMY<br>TEXT OF THE PRINTING</p><div class="price">$22.00</div></div>
    <div class="more">VIEW DETAILS</div>
  </article>
  <article class="card rose">
    <div class="shot"><div role="img" aria-label="Eyelash pack, rose edition" style="background:linear-gradient(160deg,#e4ece6,#ecd3d8)"></div></div>
    <div class="info"><p>LOREM IPSUM IS SIMPLY DUMMY<br>TEXT OF THE PRINTING</p><div class="price">$22.00</div></div>
    <div class="more">VIEW DETAILS</div>
  </article>
  <article class="card violet">
    <div class="shot"><div role="img" aria-label="Eyelash pack, violet edition" style="background:linear-gradient(160deg,#e2ece2,#e6d3e2)"></div></div>
    <div class="info"><p>LOREM IPSUM IS SIMPLY DUMMY<br>TEXT OF THE PRINTING</p><div class="price">$22.00</div></div>
    <div class="more">VIEW DETAILS</div>
  </article>
  <article class="card amber">
    <div class="shot"><div role="img" aria-label="Eyelash pack, amber edition" style="background:linear-gradient(160deg,#e2e4ee,#ece6d6)"></div></div>
    <div class="info"><p>LOREM IPSUM IS SIMPLY DUMMY<br>TEXT OF THE PRINTING</p><div class="price">$22.00</div></div>
    <div class="more">VIEW DETAILS</div>
  </article>
</section>

<section class="about">
  <h2>ABOUT VELQA</h2>
  <p>Lorem Ipsum is simply dummy text of the printing and typesetting industry. Lorem Ipsum has been the industry's standard dummy text ever since the 1500s, when an unknown printer took a galley of type and scrambled it to make a type specimen book. It has survived not only five centuries, but also the leap into electronic typesetting, remaining essentially unchanged. It was popularised in the 1960s with the release of Lettrim sheets containing Lorem Ipsum passages, and more recently with desktop publishing software like Orvel PageSetter including versions of Lorem Ipsum.</p>
</section>

<div class="rule" style="top:924px"></div>
<div class="newsletter">GET OUR RECENT UPDATES THROUGH YOUR EMAIL ID</div>
<div class="email">ENTER YOUR EMAIL ID :</div>
<div class="subscribe">SUBSCRIBE</div>
<div class="social">
  <span style="background:#2a5db0"></span><span style="background:#3aa0dc"></span><span style="background:#d01e2d"></span><span style="background:#333"></span>
</div>
<div class="rule" style="top:977px;height:2px"></div>

<footer>
  <div class="footer-col" style="left:75px"><h3>WELCOME</h3><ul><li>Home</li><li>Products</li><li>Services</li><li>Onlin E Shop</li><li>About Us</li><li>Contact Us</li></ul></div>
  <div class="footer-col" style="left:211px"><h3>OTHERS</h3><ul><li>Blog</li><li>Affiliate Program</li><li>Contact</li></ul></div>
  <div class="footer-col" style="left:353px"><h3>CUSTOMER CARE</h3><ul><li>Contact Us</li><li>Size Chart</li><li>Shipping</li><li>International</li><li>Returns</li><li>FAQ</li><li>Privacy Policy</li></ul></div>
  <div class="footer-col" style="left:501px"><h3>INFORMATION</h3><ul><li>Terms &amp; Conditions</li><li>Privacy Policy</li><li>Disclaimer</li><li>Sitemap</li></ul></div>
  <div class="footer-brand"><div class="name">VELQA</div><div class="tag">EYELASHES</div></div>
  <div class="rule" style="top:1149px"></div>
  <div class="copyright">COPYRIGHT © 2015. VELQA. ALL RIGHTS RESERVED.</div>
</footer>

</body>
</html>
```